Beauty Therapy Web Design

I need a web page design for a small beauty therapy clinic, the owner is currently the only beauty therapist working there.
We require the following pages:
Home
About
Treatments
Nails
Courses
Contact
I will attach the clinics business card, treatment menu and signage so that you get a feeling for the branding colours etc.
This is the first website for the beauty therapist, she would like to attract new clients and also tourists that come in on the cruise ships. The thing that sets her apart from other clinics is that she welcomes texting for appointments.
I have selected refundable because I have never done this before so I don't know what to expect, I have the full intention of going through with it as long as I get a good design.
Feel free to ask for further information
Reason: Project extended as I am away for work and am unable to meet with the owner.
Target Market(s)
Females 18 to 50
Industry/Entity Type
Business
Look and feel

```html
<!DOCTYPE html>
<html lang="en">
<head>
<meta charset="utf-8">
<title>Lumera Beauty Therapy – About</title>
<link href="https://fonts.googleapis.com/css2?family=Crimson+Text:ital,wght@0,400;0,600;1,400;1,600&family=Open+Sans:wght@600&display=swap" rel="stylesheet">
<style>
:root{
  --lilac:#a98bdc;
  --lilac-deep:#8f6bd3;
  --lilac-text:#9c80d6;
  --nav-text:#7a5cc4;
  --footer-text:#3b2870;
  --body-text:#4a4a4a;
  --heading:#111;
  --white:#fff;
  --photo-light:#9bc05a;
  --photo-dark:#3d5a22;
  --icon-border:#c9c9c9;
}
*{margin:0;padding:0;box-sizing:border-box}
html,body{width:1200px;height:623px;overflow:hidden;background:var(--white)}
body{position:relative;font-family:"Open Sans",Arial,sans-serif}
.top-band{position:absolute;left:10px;top:0;width:1180px;height:6px;background:var(--lilac);border-radius:0 0 6px 6px}
.brand-tab{position:absolute;left:168px;top:0;width:290px;height:126px;background:var(--lilac);border-radius:0 0 10px 10px;box-shadow:4px 6px 0 var(--lilac-deep);display:flex;flex-direction:column;justify-content:center;align-items:center}
.brand-name{font-family:"Crimson Text",Georgia,serif;font-weight:600;color:var(--white);font-size:34px;line-height:1.05;text-align:center}
.brand-name small{display:block;font-size:17px;letter-spacing:1px;font-weight:600}
.call{position:absolute;left:658px;top:10px;font-family:"Crimson Text",Georgia,serif;font-style:italic;font-weight:600;font-size:25px;color:var(--lilac-text)}
.social{position:absolute;top:0;display:flex;gap:8px;left:902px}
.social span{display:block;width:39px;height:41px;border:1px solid var(--icon-border);border-top:none;border-radius:0 0 5px 5px;background:linear-gradient(#fff,#f1f1f1);box-shadow:0 2px 3px rgba(0,0,0,.12)}
.main-nav{position:absolute;top:82px;left:0;width:1200px;font-family:"Crimson Text",Georgia,serif;font-style:italic;font-size:17px}
.main-nav a,.foot-nav a{position:absolute;text-decoration:none;white-space:nowrap}
.main-nav a{color:var(--nav-text)}
.main-nav .current::after{content:"";position:absolute;left:-3px;right:-3px;top:24px;height:4px;border-radius:2px;background:var(--lilac-deep)}
.page-title{position:absolute;left:210px;top:162px;font-family:"Crimson Text",Georgia,serif;font-style:italic;font-weight:400;font-size:25px;color:var(--heading);text-decoration:underline;text-decoration-thickness:1px;text-underline-offset:4px}
.about-copy{position:absolute;left:209px;top:205px;width:557px;font-size:12px;line-height:27.7px;color:var(--body-text);text-align:justify}
.portrait{position:absolute;left:781px;top:209px;width:272px;height:188px;border-radius:8px;background:radial-gradient(circle at 55% 45%,#d9c9a0 0,#b5c27a 30%,var(--photo-light) 55%,var(--photo-dark) 100%)}
.read-btn{position:absolute;left:674px;top:465px;width:79px;height:25px;border-radius:5px;background:linear-gradient(var(--lilac),var(--lilac-deep));color:var(--white);font-family:"Crimson Text",Georgia,serif;font-style:italic;font-size:20px;line-height:25px;text-align:center;text-decoration:none}
.footer-band{position:absolute;left:10px;top:543px;width:1180px;height:33px;background:var(--lilac);border-radius:8px;box-shadow:0 0 24px rgba(0,0,0,.18)}
.foot-nav{position:absolute;top:548px;left:0;width:1200px;font-family:"Crimson Text",Georgia,serif;font-style:italic;font-size:17px}
.foot-nav a{color:var(--footer-text)}
.copyright{position:absolute;left:0;top:590px;width:1200px;text-align:center;font-family:"Crimson Text",Georgia,serif;font-style:italic;font-size:12.5px;color:var(--footer-text)}
</style>
</head>
<body>
<div class="top-band"></div>

<header>
  <div class="brand-tab">
    <div class="brand-name">Lumera<small>BEAUTY THERAPY</small></div>
  </div>
  <div class="call">Call Us 555 014 2290</div>
  <div class="social" aria-label="Social links"><span></span><span></span><span></span></div>
  <nav class="main-nav">
    <a href="#" style="left:538px">Home</a>
    <a href="#" class="current" style="left:619px">About</a>
    <a href="#" style="left:699px">Treatments</a>
    <a href="#" style="left:815px">Nails</a>
    <a href="#" style="left:890px">Courses</a>
    <a href="#" style="left:983px">Contact</a>
  </nav>
</header>

<main>
  <h1 class="page-title">About</h1>
  <p class="about-copy">Sed ut perspiciatis unde omnis iste natus error sit voluptatem accusantium doloremque laudantium, totam rem aperiam, eaque ipsa quae ab illo inventore veritatis et quasi architecto beatae vitae dicta sunt explicabo. Nemo enim ipsam voluptatem quia voluptas sit aspernatur aut odit aut fugit, sed quia consequuntur magni dolores eos qui ratione voluptatem sequi nesciunt. Neque porro quisquam est, qui dolorem ipsum quia dolor sit amet, consectetur, adipisci velit, sed quia non numquam eius modi tempora incidunt ut labore et dolore magnam aliquam quaerat voluptatem. Ut enim ad minima veniam, quis nostrum exercitationem ullam corporis suscipit laboriosam, nisi ut aliquid ex ea commodi consequatur? Quis autem vel eum iure reprehenderit qui in ea voluptate velit esse quam nihil molestiae consequatur, vel illum qui dolorem eum fugiat quo voluptas</p>
  <div class="portrait" role="img" aria-label="Photo of a smiling client with long blonde hair among green ivy leaves"></div>
  <a href="#" class="read-btn">Read</a>
</main>

<footer>
  <div class="footer-band"></div>
  <nav class="foot-nav">
    <a href="#" style="left:367px">Home</a>
    <a href="#" style="left:442px">About</a>
    <a href="#" style="left:518px">Treatments</a>
    <a href="#" style="left:625px">Nails</a>
    <a href="#" style="left:696px">Courses</a>
    <a href="#" style="left:781px">Contact</a>
  </nav>
  <p class="copyright">Copyright © 2012.www.lumerabeautytherapy.com</p>
</footer>
</body>
</html>
```